card for handyman and landscaping business, double sided with services listed on the back

Design a business card for a handyman and Landscaping business in San Jose,ca. Would like front to be a house with 3D characters doing different tasks i.e. Mowing lawn, painting, sprinklers, lighting, weed whacking, power washing, lumber etc. on the backside a cutout of the interior with computer, internet, cleaning, bathroom/kitchen remodeling, smart home etc.

Industry/Entity Type

Handyman

Contact Information for Business Card

Two sided view of a house, one outside services and one inside services

Colors

Designer to choose colors to be used in the design.

Requirements
Must have
• General Household Repairs and Maintenance
• Landscaping, Gardening, and Planting
• Painting, Patching and Trim/Moulding Work
• Cleaning, Restoring and Hauling/Trash Removal
• Blinds, Curtains, and Assembly Work
• Computer, Internet/Wireless, and Smart Home Service

```html
<!DOCTYPE html>
<html lang="en">
<head>
<meta charset="utf-8">
<title>Handyman, Landscaping and Tech Services – Business Card</title>
<link href="https://fonts.googleapis.com/css2?family=Open+Sans:wght@400;600;700&display=swap" rel="stylesheet">
<style>
  :root{
    --backdrop:#adadad;
    --card-green:#0b4d2a;
    --roof-line:#2ea84a;
    --house-fill:#eeeeee;
    --ink-light:#ffffff;
  }
  *{margin:0;padding:0;box-sizing:border-box}
  html,body{width:1200px;height:900px;overflow:hidden}
  body{background:var(--backdrop);font-family:"Open Sans",Arial,sans-serif;position:relative}
  .card{position:absolute;top:306px;width:438px;height:272px;background:var(--card-green);
        color:var(--ink-light);overflow:hidden;box-shadow:2px 3px 5px rgba(0,0,0,.35)}
  .card--front{left:150px}
  .card--back{left:608px;width:440px}
  .house{position:absolute;left:0;top:0}
  .headline{position:absolute;left:25px;top:26px;font-size:16px;font-weight:700;letter-spacing:.1px;white-space:nowrap}
  .contact-list{position:absolute;left:22px;top:62px;list-style:none;font-size:12.5px;line-height:16px}
  .contact-list li{display:flex;align-items:center;gap:6px}
  .contact-list svg{width:9px;height:9px;fill:var(--ink-light)}
  .address{position:absolute;left:23px;top:119px;font-size:12.5px;line-height:16px}
  .person{position:absolute;right:24px;top:63px;text-align:right}
  .person__name{font-size:15px;font-weight:700;line-height:18px}
  .person__role{font-size:12.5px;line-height:16px}
  .service-list{position:absolute;top:25px;list-style:none;font-size:11.5px;line-height:14px}
  .service-list li{position:relative;padding-left:8px}
  .service-list li::before{content:"";position:absolute;left:-1px;top:5px;width:5px;height:5px;border-radius:50%;background:var(--ink-light)}
  .service-list--outside{left:18px}
  .service-list--inside{left:270px}
</style>
</head>
<body>

<section class="card card--front" aria-label="Card front">
  <svg class="house" width="438" height="272" viewBox="0 0 438 272">
    <polygon points="0,272 28,174 115,174 115,190 217,122 318,192 318,172 405,170 438,272" fill="var(--house-fill)"/>
    <polyline points="28,174 115,174 115,190 217,122 318,192 318,172 405,170" fill="none" stroke="var(--roof-line)" stroke-width="3"/>
    <g fill="var(--card-green)">
      <circle cx="55" cy="229" r="25"/><circle cx="120" cy="229" r="25"/><circle cx="186" cy="229" r="25"/>
      <circle cx="251" cy="229" r="25"/><circle cx="316" cy="229" r="25"/><circle cx="382" cy="229" r="25"/>
    </g>
    <g fill="#fff" stroke="none">
      <!-- bathroom -->
      <rect x="46" y="214" width="18" height="11" rx="1"/>
      <path d="M44 227h22c0 7-4 10-8 11v4h-6v-4c-4-1-8-4-8-11z"/>
      <!-- cleaning -->
      <path d="M129 211l2 1-9 15-2-1z"/>
      <path d="M112 229c4-4 9-3 12 0l-3 10c-5 0-10-3-12-5z"/>
      <!-- computer -->
      <rect x="173" y="215" width="26" height="18" rx="1"/>
      <rect x="181" y="235" width="10" height="3"/><rect x="176" y="238" width="20" height="2"/>
      <!-- wireless -->
      <rect x="249" y="224" width="4" height="18"/><circle cx="251" cy="222" r="3"/>
    </g>
    <g fill="none" stroke="#fff" stroke-width="2">
      <path d="M180 224a8 8 0 0 1 12 0M183 227a4 4 0 0 1 6 0" stroke="var(--card-green)"/>
      <path d="M244 215a10 10 0 0 0 0 14M258 215a10 10 0 0 1 0 14M240 211a16 16 0 0 0 0 22M262 211a16 16 0 0 1 0 22"/>
      <!-- lighting -->
      <path d="M316 208v-3M305 213l-2-2M327 213l2-2M301 223h-3M331 223h3"/>
    </g>
    <g fill="#fff">
      <path d="M316 212a10 10 0 0 1 6 18v4h-12v-4a10 10 0 0 1 6-18z"/>
      <rect x="311" y="236" width="10" height="3"/><rect x="312" y="240" width="8" height="2"/>
      <!-- smart home -->
      <path d="M382 210l16 14h-4v16h-24v-16h-4z"/>
    </g>
    <circle cx="382" cy="230" r="5" fill="none" stroke="var(--card-green)" stroke-width="2"/>
    <path d="M382 223v6" stroke="var(--card-green)" stroke-width="2"/>
  </svg>

  <h1 class="headline">HANDYMAN , LANDSCAPING AND TECH SERVICES</h1>
  <ul class="contact-list">
    <li><svg viewBox="0 0 10 10"><path d="M2 0l2 2-1 2c1 1 2 2 3 3l2-1 2 2-2 2C4 10 0 6 0 2z"/></svg>(044)987654321</li>
    <li><svg viewBox="0 0 10 10"><path d="M0 2h10v1L5 6 0 3zM0 4l5 3 5-3v4H0z"/></svg>hello@bayhomecrew.com</li>
    <li><svg viewBox="0 0 10 10"><circle cx="5" cy="5" r="5"/></svg>www.bayhomecrew.com</li>
  </ul>
  <p class="address">5678, Orchard Lane,<br>San Jose CA, 95112</p>
  <div class="person">
    <p class="person__name">DANIEL REYES</p>
    <p class="person__role">Managing Director</p>
  </div>
</section>

<section class="card card--back" aria-label="Card back">
  <svg class="house" width="440" height="272" viewBox="0 0 440 272">
    <polygon points="0,272 29,174 116,176 116,191 219,122 320,192 320,174 408,172 440,272" fill="var(--house-fill)"/>
    <polyline points="29,174 116,176 116,191 219,122 320,192 320,174 408,172" fill="none" stroke="var(--roof-line)" stroke-width="3"/>
    <g fill="var(--card-green)">
      <circle cx="56" cy="229" r="25"/><circle cx="121" cy="229" r="25"/><circle cx="187" cy="229" r="25"/>
      <circle cx="253" cy="229" r="25"/><circle cx="319" cy="229" r="25"/><circle cx="385" cy="229" r="25"/>
    </g>
    <g fill="#fff">
      <!-- mowing -->
      <path d="M38 214l2-1 10 14h-2z"/><rect x="46" y="226" width="20" height="8"/>
      <circle cx="50" cy="237" r="3"/><circle cx="66" cy="237" r="3"/>
      <!-- trim/moulding -->
      <rect x="104" y="236" width="34" height="3"/>
      <path d="M130 211l3 2-12 20-3-2z"/><path d="M113 230l6 3-4 4z"/>
      <!-- painting -->
      <rect x="176" y="213" width="20" height="8" rx="2"/>
      <path d="M196 216h3v9h-12v5h-2v-7h12v-6h-1z"/><rect x="184" y="230" width="5" height="12" rx="1"/>
      <!-- power washing -->
      <path d="M241 222h18v4h-10l-2 12h-5l2-12h-3z"/><rect x="259" y="223" width="6" height="2"/>
      <circle cx="268" cy="220" r="1"/><circle cx="270" cy="224" r="1"/><circle cx="268" cy="228" r="1"/>
      <!-- hauling -->
      <rect x="308" y="212" width="22" height="4" rx="1"/><path d="M309 218h20l-2 20h-16z"/>
      <circle cx="312" cy="239" r="3"/>
    </g>
    <!-- blinds / window -->
    <rect x="373" y="217" width="24" height="24" fill="none" stroke="#fff" stroke-width="3"/>
    <path d="M385 217v24M373 229h24" stroke="#fff" stroke-width="2"/>
  </svg>

  <ul class="service-list service-list--outside">
    <li>Handyman</li><li>Landscaping</li><li>Sprinklers/Irrigation</li><li>Painting</li>
    <li>Electrical</li><li>Lighting</li><li>Power Washing</li><li>Hauling</li>
  </ul>
  <ul class="service-list service-list--inside">
    <li>Cleaning</li><li>Bath/Kitchen</li><li>Baseboards/Trim/Moulding</li><li>Smart Home</li>
    <li>A/C and Heating</li><li>Blinds, Curtains</li><li>Assembly Services</li><li>Computer/Tech Service</li>
  </ul>
</section>

</body>
</html>
```